Flat Belly Design Graphics for Social

I want to create 9 social media graphics (new Instagram size 4:5 (1080 x 1350 pixels) focusing on our Flat Belly Graphics, using the pics attached. Use the attached pics, NO RANDOM STOCK PHOTOGRAPHY. For the color scheme of the graphics, the color palette is attached. YOU MUST POST ALL 9 GRAPHICS IN ONE ENTRY.
Using the 3 titles below, create one set of graphics. 1) with all text, then for the others, use the pictures as detailed below in IMPORTANT:
1. Ten-Week Bright Morning Reboot
2. The Quick Garden Kitchen Menu Guide
3. Studio Habits for Lasting Energy Past Midlife - Zero Gym Needed
IMPORTANT:
Only use RK Pic 1 and RK Pic 2 with the title, Ten-Week Bright Morning Reboot
Only use meal plan1 and meal plan2 pics with the title, Quick Garden Kitchen Menu Guide
Only use studio habits 1 and studio habits 2 pics with the title, Studio Habits for Lasting Energy Past Midlife - Zero Gym Needed
women over 40

```html
<!DOCTYPE html>
<html lang="en">
<head>
<meta charset="utf-8">
<title>Morning Reboot Social Set</title>
<link rel="stylesheet" href="https://fonts.googleapis.com/css2?family=Oswald:wght@300;400;500;600;700&display=swap">
<style>
  :root {
    --board: #230d15;
    --blush: #fbeff0;
    --petal: #f8d6e0;
    --rose: #e197ad;
    --rose-deep: #e06b92;
    --hot: #f38fb2;
    --forest: #25473f;
    --pine: #1e5b4b;
    --teal: #2a7563;
    --sky: #6ec7da;
    --white: #ffffff;
    --photo-warm-a: #c99a86;
    --photo-warm-b: #7c5646;
    --photo-food-a: #8a5a3e;
    --photo-food-b: #3c2a22;
  }
  * { margin: 0; padding: 0; box-sizing: border-box; }
  html, body { width: 1074px; height: 1200px; overflow: hidden; }
  body {
    background: var(--board);
    font-family: "Oswald", sans-serif;
    position: relative;
  }
  .tile {
    position: absolute;
    width: 259px;
    height: 324px;
    overflow: hidden;
  }
  .tile > svg.backdrop { position: absolute; inset: 0; width: 100%; height: 100%; }
  .col-1 { left: 122px; } .col-2 { left: 408px; } .col-3 { left: 690px; }
  .row-1 { top: 94px; } .row-2 { top: 438px; } .row-3 { top: 782px; }

  .line { position: absolute; line-height: 1; white-space: nowrap; }
  .kicker { color: var(--rose); font-weight: 600; }
  .kicker-hot { color: var(--rose-deep); font-weight: 600; }
  .heavy { color: var(--forest); font-weight: 700; }
  .thin { color: var(--forest); font-weight: 300; }
  .sub { color: var(--pine); font-weight: 600; }
  .on-rose { color: var(--white); text-shadow: 0 1px 2px rgba(0,0,0,.25); }
  .right { text-align: right; }
  .centered { left: 0; width: 259px; text-align: center; }

  .photo-slot { position: absolute; }
  .meal-band {
    position: absolute; left: 22px; width: 215px; height: 26px;
    background: var(--rose); color: var(--white);
    font-weight: 500; font-size: 21px; letter-spacing: 5px;
    text-align: center; line-height: 26px;
  }
</style>
</head>
<body>

<!-- Row 1: all-text set -->
<section class="tile col-1 row-1 reboot-text">
  <svg class="backdrop" viewBox="0 0 259 324" preserveAspectRatio="none">
    <defs>
      <radialGradient id="bubble" cx="60%" cy="45%" r="60%">
        <stop offset="0" stop-color="#f9cfdc"/><stop offset="1" stop-color="#fbe3ea"/>
      </radialGradient>
    </defs>
    <rect width="259" height="324" fill="var(--rose)"/>
    <path d="M98 0 H259 V324 H80 C40 285 18 240 30 200 C45 150 100 120 98 60 Z" fill="var(--blush)"/>
    <circle cx="232" cy="36" r="44" fill="url(#bubble)" stroke="#f4c6d4" stroke-width=".8"/>
    <circle cx="222" cy="286" r="44" fill="url(#bubble)" stroke="#f4c6d4" stroke-width=".8"/>
  </svg>
  <div class="line kicker" style="left:104px;top:70px;font-size:27px;">Ten-Week</div>
  <div class="line heavy" style="left:104px;top:100px;font-size:50px;">Bright</div>
  <div class="line heavy" style="left:106px;top:158px;font-size:40px;">Morning</div>
  <div class="line sub" style="left:48px;top:220px;font-size:35px;">Reboot</div>
</section>

<section class="tile col-2 row-1 garden-text">
  <svg class="backdrop" viewBox="0 0 259 324" preserveAspectRatio="none">
    <rect width="259" height="324" fill="var(--rose)"/>
    <path d="M98 0 H259 V324 H80 C40 285 18 240 30 200 C45 150 100 120 98 60 Z" fill="var(--blush)"/>
    <circle cx="232" cy="36" r="44" fill="url(#bubble)" stroke="#f4c6d4" stroke-width=".8"/>
    <circle cx="222" cy="286" r="44" fill="url(#bubble)" stroke="#f4c6d4" stroke-width=".8"/>
  </svg>
  <div class="line kicker" style="left:104px;top:78px;font-size:19px;">The Quick</div>
  <div class="line thin" style="left:104px;top:100px;font-size:52px;">Garden</div>
  <div class="line heavy" style="left:106px;top:164px;font-size:44px;">Kitchen</div>
  <div class="line sub" style="left:48px;top:228px;font-size:34px;">Menu Guide</div>
</section>

<section class="tile col-3 row-1 studio-text">
  <svg class="backdrop" viewBox="0 0 259 324" preserveAspectRatio="none">
    <rect width="259" height="324" fill="var(--rose)"/>
    <path d="M98 0 H259 V324 H80 C40 285 18 240 30 200 C45 150 100 120 98 60 Z" fill="var(--blush)"/>
    <circle cx="232" cy="36" r="44" fill="url(#bubble)" stroke="#f4c6d4" stroke-width=".8"/>
    <circle cx="222" cy="286" r="44" fill="url(#bubble)" stroke="#f4c6d4" stroke-width=".8"/>
  </svg>
  <div class="line kicker" style="left:107px;top:54px;font-size:19px;line-height:1.15;">Studio<br>Habits for</div>
  <div class="line thin" style="left:107px;top:100px;font-size:50px;">Lasting</div>
  <div class="line heavy" style="left:109px;top:160px;font-size:46px;">Energy</div>
  <div class="line sub" style="left:49px;top:228px;font-size:19px;line-height:1.2;">Past Midlife - Zero Gym<br>Needed</div>
</section>

<!-- Row 2 -->
<section class="tile col-1 row-2 reboot-portrait">
  <svg class="backdrop" viewBox="0 0 259 324" preserveAspectRatio="none">
    <rect width="259" height="324" fill="var(--rose)"/>
    <path d="M0 0 H70 C100 30 110 70 150 60 C200 48 235 110 230 160 C225 215 170 235 130 245 C100 252 85 290 80 324 H0 Z" fill="var(--petal)"/>
    <circle cx="190" cy="150" r="98" fill="none" stroke="#f6c9d6" stroke-width="1"/>
  </svg>
  <div class="photo-slot" role="img" aria-label="Photo of a smiling woman in a white cropped sweater pointing to her midsection"
       style="left:100px;top:58px;width:184px;height:184px;border-radius:50%;background:radial-gradient(circle at 50% 40%, #f3ece8 0 30%, var(--photo-warm-a) 55%, #2b2220 100%);"></div>
  <div class="line kicker" style="left:13px;top:72px;font-size:25px;">Ten-Week</div>
  <div class="line heavy" style="left:13px;top:104px;font-size:40px;">Bright</div>
  <div class="line thin" style="left:14px;top:156px;font-size:30px;">Morning</div>
  <div class="line on-rose" style="left:120px;top:262px;font-size:32px;font-weight:600;">Reboot</div>
</section>

<section class="tile col-2 row-2 garden-photo">
  <svg class="backdrop" viewBox="0 0 259 324" preserveAspectRatio="none">
    <rect width="259" height="324" fill="var(--blush)"/>
  </svg>
  <div class="photo-slot" role="img" aria-label="Overhead photo of fresh vegetables, fish and a meal plan notepad on a wooden table"
       style="left:0;top:130px;width:259px;height:194px;background:radial-gradient(circle at 50% 50%, var(--photo-food-b) 0 35%, #8b4a30 70%, #b8462f 100%);"></div>
  <svg class="backdrop" viewBox="0 0 259 324" preserveAspectRatio="none">
    <path d="M0 0 H259 V130 C240 180 190 190 140 178 C90 166 40 140 0 145 Z" fill="var(--hot)"/>
    <path d="M0 0 H259 V128 C240 170 190 178 140 166 C90 154 40 128 0 134 Z" fill="var(--blush)"/>
  </svg>
  <div class="line kicker-hot right" style="right:14px;top:22px;font-size:24px;color:var(--hot);">The Quick</div>
  <div class="line thin right" style="right:12px;top:50px;font-size:40px;">Garden Kitchen</div>
  <div class="line heavy right" style="right:14px;top:112px;font-size:32px;color:var(--pine);">Menu Guide</div>
</section>

<section class="tile col-3 row-2 studio-photo">
  <svg class="backdrop" viewBox="0 0 259 324" preserveAspectRatio="none">
    <rect width="259" height="324" fill="var(--petal)"/>
  </svg>
  <div class="photo-slot" role="img" aria-label="Photo of one woman whispering a secret to a surprised friend"
       style="left:0;top:0;width:230px;height:160px;border-radius:0 0 90px 0;background:linear-gradient(135deg,#f4f1ef 0%,var(--photo-warm-a) 55%,var(--photo-warm-b) 100%);"></div>
  <svg class="backdrop" viewBox="0 0 259 324" preserveAspectRatio="none">
    <path d="M0 180 C10 150 40 145 70 150 C120 160 160 150 200 130 C230 118 259 130 259 140 V324 H0 Z" fill="var(--petal)"/>
  </svg>
  <div class="line kicker-hot right" style="right:14px;top:175px;font-size:18px;">Studio Habits for</div>
  <div class="line heavy right" style="right:14px;top:196px;font-size:34px;">Lasting Energy</div>
  <div class="line sub right" style="right:14px;top:252px;font-size:19px;line-height:1.2;">Past Midlife -<br>Zero Gym Needed</div>
</section>

<!-- Row 3 -->
<section class="tile col-1 row-3 reboot-kitchen">
  <svg class="backdrop" viewBox="0 0 259 324" preserveAspectRatio="none">
    <rect width="259" height="324" fill="var(--petal)"/>
    <path d="M118 0 H259 V324 C225 300 205 250 170 205 C140 165 100 150 110 100 C115 70 110 30 118 0 Z" fill="var(--rose)"/>
    <circle cx="90" cy="150" r="98" fill="none" stroke="var(--rose)" stroke-width="1"/>
  </svg>
  <div class="photo-slot" role="img" aria-label="Photo of a smiling woman in a white cropped sweater standing in a kitchen"
       style="left:-4px;top:56px;width:188px;height:188px;border-radius:50%;background:radial-gradient(circle at 50% 45%, #f3ece8 0 28%, var(--photo-warm-a) 55%, #5b3e30 100%);"></div>
  <div class="line on-rose" style="left:145px;top:30px;font-size:26px;font-weight:500;">Ten-Week</div>
  <div class="line on-rose" style="left:145px;top:62px;font-size:40px;font-weight:700;">Bright</div>
  <div class="line on-rose" style="left:145px;top:112px;font-size:30px;font-weight:300;">Morning</div>
  <div class="line sub" style="left:13px;top:268px;font-size:30px;">Reboot</div>
</section>

<section class="tile col-2 row-3 garden-guide">
  <svg class="backdrop" viewBox="0 0 259 324" preserveAspectRatio="none">
    <rect width="259" height="324" fill="var(--petal)"/>
  </svg>
  <div class="photo-slot" role="img" aria-label="Overhead photo of chicken, berries, asparagus and a printed meal plan sheet on a wooden table"
       style="left:0;top:0;width:259px;height:160px;background:radial-gradient(circle at 55% 55%, #f1ece6 0 20%, var(--photo-food-a) 55%, var(--photo-food-b) 100%);"></div>
  <svg class="backdrop" viewBox="0 0 259 324" preserveAspectRatio="none">
    <path d="M0 150 C20 110 70 100 110 110 C160 125 190 170 259 110 V175 C240 170 215 180 190 170 C140 150 80 150 0 160 Z" fill="var(--rose)"/>
    <path d="M0 145 C30 130 70 115 110 130 C150 140 170 165 200 170 C230 175 250 165 259 160 V324 H0 Z" fill="var(--petal)"/>
  </svg>
  <div class="line centered" style="top:180px;font-size:36px;font-weight:600;color:var(--teal);">The Quick</div>
  <div class="line centered" style="top:226px;font-size:30px;font-weight:700;color:var(--forest);">GARDEN KITCHEN</div>
  <div class="meal-band" style="top:270px;">Menu Guide</div>
</section>

<section class="tile col-3 row-3 studio-caps">
  <svg class="backdrop" viewBox="0 0 259 324" preserveAspectRatio="none">
    <rect width="259" height="324" fill="var(--sky)"/>
  </svg>
  <div class="photo-slot" role="img" aria-label="Photo of a woman whispering to a surprised friend against a blue backdrop"
       style="left:60px;top:0;width:180px;height:150px;background:radial-gradient(ellipse at 50% 60%, #e9c4b4 0 30%, #b07f6a 60%, var(--sky) 100%);"></div>
  <svg class="backdrop" viewBox="0 0 259 324" preserveAspectRatio="none">
    <path d="M0 0 H25 C15 40 30 90 60 110 C100 140 150 150 190 140 C225 132 255 135 255 170 C255 220 220 280 205 324 H0 Z" fill="var(--petal)"/>
  </svg>
  <div class="line kicker-hot" style="left:14px;top:166px;font-size:19px;">Studio Habits for</div>
  <div class="line heavy" style="left:14px;top:190px;font-size:31px;">LASTING ENERGY</div>
  <div class="line sub" style="left:15px;top:236px;font-size:16px;">Past Midlife - Zero Gym Needed</div>
</section>

</body>
</html>
```